Full re-design of visual identity

We have just re-designed our logo and would like to apply it on our folders, business cards, stationery, and etc... we are attaching new logo + the material we need to re-design... we will provide full corel draw files to help make job easier and also because lot of icons and artwork can be still used...

any doubts we are at your disposal. thanks in advance.

```html
<!DOCTYPE html>
<html lang="pt">
<head>
<meta charset="utf-8">
<title>Korvalink – Stationery</title>
<link rel="stylesheet" href="https://fonts.googleapis.com/css2?family=Arimo:wght@400;700&display=swap">
<style>
  :root{
    --bg:#7d8186;
    --paper:#ffffff;
    --orange:#f47a12;
    --orange-deep:#e2541c;
    --grey:#6f6f6f;
    --ink:#1e1e1e;
    --muted:#555;
    --tab:#8a8a8a;
  }
  *{box-sizing:border-box;margin:0;padding:0}
  html,body{width:1200px;height:1071px;overflow:hidden}
  body{background:var(--bg);font-family:"Arimo",Arial,sans-serif;position:relative;color:var(--ink)}
  .sheet{position:absolute;background:var(--paper);overflow:hidden}

  .brand{position:absolute;display:flex;flex-direction:column;align-items:flex-start}
  .brand-row{display:flex;align-items:center;gap:.18em}
  .brand-name{font-weight:700;color:var(--grey);letter-spacing:-.02em;line-height:1}
  .brand-dot{width:.55em;height:.55em;border-radius:50%;background:var(--orange)}
  .brand-tag{color:var(--grey);font-size:9px;margin-top:2px;padding-left:8px}

  .corner-circle{position:absolute;border-radius:50%;background:linear-gradient(90deg,var(--orange-deep),var(--orange))}

  /* Letterhead */
  .letterhead{left:83px;top:78px;width:498px;height:706px}
  .letterhead .brand{left:145px;top:60px}
  .letterhead .brand-name{font-size:46px}
  .letter{position:absolute;left:54px;top:179px;width:397px;font-size:12.4px;line-height:15.6px}
  .letter .salutation{font-weight:700;margin-bottom:21px}
  .letter p{text-align:justify;margin-bottom:15.6px}
  .letter .closing{font-weight:700;margin-top:22px}
  .signature{position:absolute;left:54px;top:520px;width:106px;height:38px;background:linear-gradient(90deg,#cfe3ee,#eef6fa)}
  .footer-rule{position:absolute;height:1px;background:var(--orange)}
  .footer{position:absolute;text-align:center;color:var(--muted)}
  .footer strong{color:var(--ink)}
  .footer .label{color:var(--orange)}
  .letterhead .footer-rule{left:181px;right:0;top:626px}
  .letterhead .footer{left:181px;right:0;top:637px;font-size:8px;line-height:12px}
  .letterhead .corner-circle{width:96px;height:96px;left:52px;top:588px}

  /* Business card front */
  .card-front{left:712px;top:114px;width:335px;height:205px}
  .card-front .brand{left:22px;top:20px}
  .card-front .brand-name{font-size:36px}
  .card-front .brand-tag{font-size:8px}
  .role{position:absolute;right:14px;top:69px;text-align:right}
  .role b{display:block;color:var(--orange);font-size:13.5px}
  .role span{color:var(--grey);font-size:12px}
  .tab{position:absolute;right:0;width:9px;background:var(--tab)}
  .card-front .tab{top:72px;height:24px}
  .contact{position:absolute;left:21px;top:106px;font-size:8.6px;line-height:10.4px;color:#333}
  .contact strong{color:var(--ink)}
  .contact ul{list-style:none;margin-top:8px}
  .contact li{display:flex;align-items:center;gap:4px}
  .contact svg{width:7px;height:7px;fill:var(--orange)}
  .card-band{position:absolute;left:0;right:0;bottom:0;height:19px;background:var(--orange)}

  /* Business card back */
  .card-back{left:712px;top:397px;width:335px;height:204px;background:var(--orange)}
  .card-back .brand{left:40px;top:72px}
  .card-back .brand-name{font-size:52px;color:#fff}
  .card-back .brand-dot{background:#fff}
  .card-back .brand-tag{color:#fff;font-size:11px;padding-left:10px}
  .card-back .tab{top:68px;height:64px}

  /* Compliment slip */
  .slip{left:285px;top:813px;width:408px;height:204px}
  .slip .brand{left:229px;top:30px}
  .slip .brand-name{font-size:31px}
  .slip .brand-tag{font-size:7px}
  .slip .corner-circle{width:75px;height:75px;left:20px;top:124px}
  .slip .footer-rule{left:114px;right:14px;top:154px}
  .slip .footer{left:114px;right:14px;top:162px;font-size:6px;line-height:9px}

  /* Envelope */
  .envelope{left:724px;top:675px;width:406px;height:285px;background:transparent;overflow:visible}
  .envelope svg{position:absolute;inset:0}
  .envelope .brand{left:233px;top:221px}
  .envelope .brand-name{font-size:28px}
  .envelope .brand-tag{font-size:6px}
</style>
</head>
<body>

<section class="sheet letterhead" aria-label="Letterhead">
  <div class="brand">
    <div class="brand-row"><span class="brand-name">korvalink</span><span class="brand-dot"></span></div>
    <span class="brand-tag">telecom · tecnologia · internet</span>
  </div>
  <div class="letter">
    <p class="salutation">Dear Someone&nbsp; Somebody</p>
    <p>Proin gravida nibh vel velit auctor aliquet. Aenean sollicitudin, lorem quis bibendum auctor, nisi elit consequat ipsum, nec sagittis sem nibh id elit. Duis sed odio sit amet nibh vulputate cursus a sit amet mauris. Morbi accumsan ipsum velit. Nam nec tellus a odio tincidunt auctor a ornare odio. Sed non&nbsp; mauris vitae erat consequat auctor eu in elit.</p>
    <p>Class aptent taciti sociosqu ad litora torquent per conubia nostra, per inceptos himenaeos. Mauris in erat justo. Nullam ac urna eu felis dapibus condimentum sit amet a augue. Sed non neque elit. Sed ut imperdiet nisi. Proin condimentum fermentum nunc. Etiam pharetra, erat sed fermentum feugiat, velit mauris egestas quam, ut aliquam massa nisl quis neque. Suspendisse in orci enim. Proin gravida nibh vel velit auctor aliquet. Aenean sollicitudin, lorem quisbibendum auctor, nisi elit consequat ipsum, nec sagittis sem nibh id elit. Duis sed odio sit amet nibh vulputate cursus a sit amet mauris. Morbi accumsan ipsum velit.</p>
    <p class="closing">Your Sincerely,<br>Somebody,</p>
  </div>
  <div class="signature" role="img" aria-label="Handwritten signature"></div>
  <div class="corner-circle"></div>
  <div class="footer-rule"></div>
  <div class="footer">
    <strong>Korvalink-Telecomunicações e internet</strong><br>
    Rua das Acácias,415 - jd.Primavera CEP 13210-400 - Varzelia - SP<br>
    <span class="label">Tel:</span> (11) 5023-7714 &nbsp; <span class="label">Email:</span> contato@korvalink.com.br <span class="label">Website:</span> www.korvalink.com.br
  </div>
</section>

<section class="sheet card-front" aria-label="Business card front">
  <div class="brand">
    <div class="brand-row"><span class="brand-name">korvalink</span><span class="brand-dot"></span></div>
    <span class="brand-tag">telecom · tecnologia · internet</span>
  </div>
  <div class="role"><b>Atendimento</b><span>Manager</span></div>
  <div class="tab"></div>
  <div class="contact">
    <strong>Korvalink-Telecomunicações e internet</strong><br>
    Rua das Acácias,415 - jd.Primavera<br>
    CEP 13210-400 - Varzelia - SP
    <ul>
      <li><svg viewBox="0 0 10 10"><path d="M2 0l2 2.5-1 1.2a6 6 0 0 0 3.3 3.3l1.2-1L10 8 8.5 10C4 10 0 6 0 1.5z"/></svg>(11) 5023-7714</li>
      <li><svg viewBox="0 0 10 10"><rect x="0" y="2" width="10" height="6"/></svg>contato@korvalink.com.br</li>
      <li><svg viewBox="0 0 10 10"><circle cx="5" cy="5" r="5"/></svg>www.korvalink.com.br</li>
    </ul>
  </div>
  <div class="card-band"></div>
</section>

<section class="sheet card-back" aria-label="Business card back">
  <div class="brand">
    <div class="brand-row"><span class="brand-name">korvalink</span><span class="brand-dot"></span></div>
    <span class="brand-tag">telecom · tecnologia · internet</span>
  </div>
  <div class="tab"></div>
</section>

<section class="sheet envelope" aria-label="Envelope">
  <svg width="406" height="285" viewBox="0 0 406 285">
    <defs>
      <linearGradient id="flap" x1="0" y1="0" x2="0" y2="1">
        <stop offset="0" stop-color="#f6911f"/>
        <stop offset=".45" stop-color="#ef5b1e"/>
        <stop offset="1" stop-color="#f47a12"/>
      </linearGradient>
    </defs>
    <path d="M10 0H396Q406 0 406 10V285H0V10Q0 0 10 0Z" fill="url(#flap)"/>
    <path d="M28 140H378L406 285H0Z" fill="#fff"/>
  </svg>
  <div class="brand">
    <div class="brand-row"><span class="brand-name">korvalink</span><span class="brand-dot"></span></div>
    <span class="brand-tag">telecom · tecnologia · internet</span>
  </div>
</section>

<section class="sheet slip" aria-label="Compliment slip">
  <div class="brand">
    <div class="brand-row"><span class="brand-name">korvalink</span><span class="brand-dot"></span></div>
    <span class="brand-tag">telecom · tecnologia · internet</span>
  </div>
  <div class="corner-circle"></div>
  <div class="footer-rule"></div>
  <div class="footer">
    <strong>Korvalink-Telecomunicações e internet</strong><br>
    Rua das Acácias,415 - jd.Primavera CEP 13210-400 - Varzelia - SP<br>
    <span class="label">Tel:</span> (11) 5023-7714 &nbsp; <span class="label">Email:</span> contato@korvalink.com.br <span class="label">Website:</span> www.korvalink.com.br
  </div>
</section>

</body>
</html>
```